Satchel & Sundial needs new business card design

I need a new business card design. I'm looking for out-of-the-box design which represents the freedom of being a location independent entrepreneur.
I offer coaching, retreats and trips.
I would like to see designs with and without the photo.
Colors I use are black (#000000), green (#25A796) and brown (#D7C38C)
Website satchelandsundial.example

Target Market(s)

location independent entrepreneurs, digital nomads, people looking to swap the 9 to 5 for a lifestyle business

Industry/Entity Type

Business

Contact Information for Business Card

Dorota Falkner
Your Lifestyle Business Coach, Retreat & Trip Leader
http://satchelandsundial.example
hello@satchelandsundial.example
Live a life you don't need a holiday from

Font styles to use
Serif
Sans Serif

Requirements
Must have
• One side should contain only the logo. I would also consider having the "Live a life you don't need a holiday from" on that side too (depending on how it looks)
• Please show both sides on the designs.

```html
<!DOCTYPE html>
<html lang="en">
<head>
<meta charset="utf-8">
<title>Satchel &amp; Sundial — Business Card</title>
<link href="https://fonts.googleapis.com/css2?family=Questrial&display=swap" rel="stylesheet">
<style>
  :root {
    --teal: #25A796;
    --teal-deep: #1f9a89;
    --ink: #222222;
    --black: #000000;
    --paper: #ffffff;
    --backdrop: #ece8df;
  }
  * { margin: 0; padding: 0; box-sizing: border-box; }
  html, body { width: 1200px; height: 1023px; overflow: hidden; }
  body {
    background: var(--backdrop);
    font-family: "Questrial", "Century Gothic", sans-serif;
    color: var(--ink);
    position: relative;
  }
  .card {
    position: absolute;
    left: 220px;
    width: 760px;
    height: 434px;
    overflow: hidden;
    box-shadow: 0 10px 28px rgba(0,0,0,0.18);
  }
  .card--front { top: 48px; background: var(--paper); }
  .card--back  { top: 536px; background: var(--teal); }

  .brand-name {
    position: absolute;
    font-size: 44px;
    line-height: 1.1;
    letter-spacing: 0.5px;
    white-space: nowrap;
  }
  .card--front .brand-name { left: 56px; top: 176px; color: var(--ink); }

  .details { position: absolute; left: 420px; top: 92px; font-size: 15px; line-height: 1.45; }
  .details .person { color: var(--teal); font-size: 24px; margin-bottom: 4px; }
  .details .role { margin-bottom: 20px; }
  .contact { list-style: none; margin-bottom: 22px; }
  .contact li { display: flex; align-items: center; gap: 8px; }
  .contact svg { width: 14px; height: 14px; flex: none; }
  .address { line-height: 1.4; }

  .band {
    position: absolute; left: 0; bottom: 0;
    width: 100%; height: 22px; background: var(--teal);
  }
  .band__tab {
    position: absolute; left: 458px; bottom: 0;
    width: 34px; height: 22px; background: var(--black);
  }

  .card--back .brand-name {
    left: 0; width: 100%; top: 170px;
    text-align: center; color: var(--paper); font-size: 56px;
  }
  .tagline {
    position: absolute; left: 40px; bottom: 34px;
    color: var(--paper); font-size: 15px; letter-spacing: 0.3px;
  }
</style>
</head>
<body>

<section class="card card--front" aria-label="Card front">
  <div class="brand-name">Satchel &amp; Sundial</div>

  <div class="details">
    <p class="person">Dorota Falkner</p>
    <p class="role">Your Lifestyle Business Coach,<br>Retreat &amp; Trip Leader</p>
    <ul class="contact">
      <li>
        <svg viewBox="0 0 16 16" aria-hidden="true"><path d="M4 1.5l2.2 3-1.3 1.6c.8 1.9 2.3 3.4 4.2 4.3l1.6-1.3 3 2.2-1.2 2.8C6.8 14 2 9.2 1.2 3.4z" fill="var(--teal)"/></svg>
        +987 21 40 63 5
      </li>
      <li>
        <svg viewBox="0 0 16 16" aria-hidden="true"><rect x="1" y="3" width="14" height="10" fill="var(--teal)"/><path d="M1.5 3.5L8 9l6.5-5.5" stroke="#fff" stroke-width="1.3" fill="none"/></svg>
        hello@satchelandsundial.example
      </li>
      <li>
        <svg viewBox="0 0 16 16" aria-hidden="true"><circle cx="8" cy="8" r="7" fill="var(--teal)"/><path d="M1 8h14M8 1c-3 3.5-3 10.5 0 14M8 1c3 3.5 3 10.5 0 14" stroke="#fff" stroke-width="1" fill="none"/></svg>
        www.satchelandsundial.example
      </li>
    </ul>
    <p class="address">Here your company or<br>home address</p>
  </div>

  <div class="band"><div class="band__tab"></div></div>
</section>

<section class="card card--back" aria-label="Card back">
  <div class="brand-name">Satchel &amp; Sundial</div>
  <p class="tagline">Live a life you don't need a holiday from</p>
</section>

</body>
</html>
```